4D Cradle Glimpse Luxury Ultrasound Billboard

Design a HIGH-END, MODERN billboard for my private prenatal ultrasound studio, 4D Cradle Glimpse, located in Pace, Florida.
This billboard will be viewed by drivers traveling at highway speeds, so it must be extremely clean, simple, and readable within 6 seconds.
About My Business
4D Cradle Glimpse is a private prenatal ultrasound studio specializing in:
Highest technology 4D/HD Ultrasounds
Early Gender Determination
Pregnancy Confirmation
I have been serving families for nearly 10 years and is known for creating a memorable experience, not just an ultrasound appointment.
Design Style
I DO NOT want:
Flowers
Leaves
Swirls
Glitter
Hearts everywhere
Busy backgrounds
Generic maternity stock graphics
I DO want:
Modern
Luxury
Upscale
Clean
Professional
Eye-catching
Premium medical spa feel
Colors
Use colors from my logo:
LOGO Green ( or a deep green)
Black
White
Soft Gold accents
Images:
Incorporate my professional headshot in a clean, modern way, logo, and the ultrasound images
Text
Keep wording minimal.
Primary Headline ( OPEN TO IDEAS) :
EXAMPLES ( WOULD RATHER SOMETHING MORE CATCHY)
" ADVANCED IMAGING. UNFORGETTABLE MOMENTS"
"MEET YOUR BABY BEFORE BIRTH"
Under headline:
4D Ultrasound • Early Gender • Pregnancy Confirmation
Business Name:
4D Cradle Glimpse
Private Prenatal Ultrasound Studio
Phone Number:
850-471-5923
Important
This billboard must be readable in 5–6 seconds from a moving vehicle.
Less text is better.
The phone number and business name must be visible from a distance.
The design should feel like a premium brand that immediately tells expecting parents:
“This is where I go to see my baby.”
Files Provided
Official logo
Headshot
Ultrasound images
Don’t make this look like a medical office billboard.
Make it look like a luxury baby experience billboard. That’s what separates 4D Cradle Glimpse from hospitals, OB offices, and all the new studios popping up around you. The emotional connection is what gets moms to book. ❤️
Billboard Size - 10.6” x 36”

```html
<!DOCTYPE html>
<html lang="en">
<head>
<meta charset="utf-8">
<title>4D Cradle Glimpse Billboard</title>
<link rel="stylesheet" href="https://fonts.googleapis.com/css2?family=Archivo:wdth,wght@62..125,500..900&display=swap">
<style>
  :root {
    --gold: #c79a3a;
    --slate-green: #5f716a;
    --white: #ffffff;
    --ink: #1a1a1a;
    --page: #ffffff;
  }
  * { margin: 0; padding: 0; box-sizing: border-box; }
  html, body {
    width: 1200px; height: 417px; overflow: hidden;
    background: var(--page);
  }
  .billboard {
    position: absolute; left: 35px; top: 43px;
    width: 1128px; height: 333px;
    background: var(--white);
    border: 1.5px solid var(--ink);
    overflow: hidden;
    font-family: "Archivo", Arial, sans-serif;
  }
  .billboard__art { position: absolute; inset: 0; }
  .headline { font-family: "Archivo", Arial, sans-serif; font-weight: 800; }
  .headline--top { font-size: 86px; fill: var(--gold); }
  .headline--bottom { font-size: 104px; fill: var(--slate-green); }
  .services { font-family: "Archivo", Arial, sans-serif; font-weight: 700; font-size: 31px; fill: var(--slate-green); }
  .services .dot { fill: var(--gold); }
  .phone { font-family: "Archivo", Arial, sans-serif; font-weight: 900; font-size: 64px; fill: var(--white); }
  .brand-card {
    position: absolute; left: 884px; top: 197px;
    width: 232px; height: 114px;
    background: var(--white);
    border: 1.5px solid var(--slate-green);
    border-radius: 16px;
    text-align: center;
  }
  .brand-card__name {
    margin-top: 12px;
    color: var(--gold); font-weight: 800; font-size: 27px;
    line-height: 29px;
  }
  .brand-card__rule {
    width: 200px; height: 1px; margin: 8px auto 6px;
    background: var(--gold);
  }
  .brand-card__tagline {
    color: var(--slate-green); font-weight: 600; font-size: 10.5px;
    letter-spacing: 0.5px;
  }
</style>
</head>
<body>
<main class="billboard">
  <svg class="billboard__art" width="1128" height="333" viewBox="0 0 1128 333">
    <defs>
      <linearGradient id="portrait-tone" x1="0" y1="0" x2="1" y2="1">
        <stop offset="0" stop-color="#eceeee"/>
        <stop offset="0.45" stop-color="#cdbb9c"/>
        <stop offset="1" stop-color="#2f4a39"/>
      </linearGradient>
      <radialGradient id="scan-tone" cx="0.45" cy="0.45" r="0.7">
        <stop offset="0" stop-color="#e9a488"/>
        <stop offset="0.6" stop-color="#b8604a"/>
        <stop offset="1" stop-color="#5a1f18"/>
      </radialGradient>
    </defs>
    <rect class="phone-band" x="140" y="259" width="988" height="74" fill="var(--slate-green)"/>
    <path class="portrait-frame" d="M0 0 H198 C252 44 258 210 152 333 H0 Z" fill="var(--slate-green)"/>
    <path class="portrait" role="img" aria-label="Portrait of the sonographer in green scrubs holding an ultrasound probe"
          d="M0 0 H192 C244 44 248 210 144 333 H0 Z" fill="url(#portrait-tone)"/>
    <circle class="scan-photo" role="img" aria-label="4D ultrasound image of a baby's face"
            cx="306" cy="223" r="92" fill="url(#scan-tone)" stroke="var(--gold)" stroke-width="2"/>

    <text class="headline headline--top" x="359" y="81" textLength="752" lengthAdjust="spacingAndGlyphs">MEET YOUR BABY</text>
    <text class="headline headline--bottom" x="359" y="168" textLength="752" lengthAdjust="spacingAndGlyphs">BEFORE BIRTH</text>
    <line class="headline-rule" x1="359" y1="181" x2="1111" y2="181" stroke="var(--gold)" stroke-width="1.5"/>

    <text class="services" x="396" y="214" textLength="478" lengthAdjust="spacingAndGlyphs"><tspan class="dot">•</tspan> 4D Ultrasound <tspan class="dot">•</tspan> Early Gender</text>
    <text class="services" x="396" y="248" textLength="404" lengthAdjust="spacingAndGlyphs"><tspan class="dot">•</tspan> Pregnancy Confirmation</text>

    <g class="phone-icon" transform="translate(378 297)">
      <circle r="19" fill="var(--white)"/>
      <path d="M-8 -9 l4 -2 l4 6 l-3 3 c1 4 4 7 8 8 l3 -3 l6 4 l-2 4 c-11 2 -22 -9 -20 -20 z"
            fill="var(--slate-green)"/>
      <path d="M3 -9 a7 7 0 0 1 7 7 M3 -13 a11 11 0 0 1 11 11" fill="none"
            stroke="var(--slate-green)" stroke-width="1.8" stroke-linecap="round"/>
    </g>
    <text class="phone" x="414" y="316" textLength="444" lengthAdjust="spacingAndGlyphs">850-471-5923</text>
  </svg>

  <div class="brand-card">
    <p class="brand-card__name">4D<br>Cradle Glimpse</p>
    <div class="brand-card__rule"></div>
    <p class="brand-card__tagline">PRENATAL ULTRASOUND STUDIO</p>
  </div>
</main>
</body>
</html>
```